Business Card - Business Consultancy

Newly Established Company, specializing in Business Consultancy, Human Resource Management, Talent Acquisition and Payroll Solutions.

We need a Business card design which portrays "elegance" and a very sleek yet business-like design. We would like a nice blue trimming (which goes well with the logo) to separate the content of the business card at the top. We would also like to see the design using the color silver either as a background or incorporated into it.

The final design should be a Business card which has colors matching the logo; a nice font; the above-mentioned specifics that adheres to the theme of "a stylish and professional business"

FYI: please do not have too fanciful designs.

Industry/Entity Type

Business Consultant

Contact Information for Business Card

Darren Lim
Business Development Director
Arbor Talent Consulting Private Limited
27 Wexley Street, #05-03B
Harbourgate Trade Building
Singapore 059317
Mobile : (+65) 98354417
Email : dlim@arbortalent-advisory.com
Alternative : arbortalentadvisory@mailbox-example.com

Requirements
Must have
• Nice Blue Trimming matching Logo which separates content, see attached
• Design incorporates either a silver background or the use of the color silver
Should not have
• No Fanciful Designs
• No Childish Designs
• No Overly Complicated Designs

```html
<!DOCTYPE html>
<html lang="en">
<head>
<meta charset="utf-8">
<title>Arbor Talent Consulting – Business Card</title>
<link href="https://fonts.googleapis.com/css2?family=Source+Sans+3:wght@400;600&display=swap" rel="stylesheet">
<style>
  :root {
    --page-bg: #d6d7d9;
    --card-bg: #111213;
    --card-edge: #1c1d1f;
    --brand-blue: #1e8fd6;
    --brand-green: #7cc242;
    --silver: #c3c7cc;
    --silver-dark: #7d8288;
    --text-light: #eef0f2;
  }
  * { box-sizing: border-box; margin: 0; padding: 0; }
  html, body {
    width: 1200px;
    height: 814px;
    overflow: hidden;
    background: var(--page-bg);
    font-family: "Source Sans 3", "Helvetica Neue", Arial, sans-serif;
  }
  .canvas {
    position: relative;
    width: 1200px;
    height: 814px;
  }
  .card {
    position: absolute;
    top: 252px;
    width: 540px;
    height: 310px;
    overflow: hidden;
    background: var(--card-bg);
    border: 1px solid var(--card-edge);
    box-shadow: 0 10px 24px rgba(0,0,0,0.25);
    color: var(--text-light);
  }
  .card--contact { left: 40px; }
  .card--brand { left: 620px; }

  /* Brand lockup */
  .brand {
    display: flex;
    align-items: center;
    gap: 10px;
  }
  .brand__dot {
    flex: none;
    border-radius: 50%;
    background: var(--brand-blue);
  }
  .brand__name {
    font-weight: 600;
    color: var(--silver);
    line-height: 1.05;
  }

  /* Contact side */
  .card--contact .brand {
    position: absolute;
    left: 28px;
    top: 136px;
  }
  .card--contact .brand__dot { width: 36px; height: 36px; }
  .card--contact .brand__name { font-size: 19px; width: 112px; }

  .divider {
    position: absolute;
    left: 198px;
    top: 28px;
    width: 2px;
    height: 254px;
    background: linear-gradient(180deg, transparent, var(--silver) 20%, var(--silver-dark) 60%, transparent);
  }

  .contact {
    position: absolute;
    left: 214px;
    top: 40px;
    right: 12px;
    font-size: 13px;
    line-height: 1.36;
  }
  .contact__name {
    color: var(--brand-blue);
    font-weight: 600;
    font-size: 18px;
    line-height: 1.2;
  }
  .contact__title {
    color: var(--brand-green);
    margin-bottom: 6px;
  }
  .contact__address { font-style: normal; margin-bottom: 6px; }
  .contact__line {
    display: flex;
    align-items: center;
    gap: 7px;
    white-space: nowrap;
  }
  .contact__icon { flex: none; width: 12px; height: 12px; }
  .contact__alt { white-space: nowrap; }

  /* Brand side */
  .card--brand .brand {
    position: absolute;
    left: 150px;
    top: 96px;
  }
  .card--brand .brand__dot { width: 56px; height: 56px; }
  .card--brand .brand__name { font-size: 28px; width: 170px; }
  .website {
    position: absolute;
    left: 0;
    right: 0;
    top: 206px;
    text-align: center;
    font-size: 14px;
    letter-spacing: 0.04em;
    color: var(--text-light);
  }
</style>
</head>
<body>
  <main class="canvas">
    <section class="card card--contact" aria-label="Business card, contact side">
      <div class="brand">
        <span class="brand__dot" aria-hidden="true"></span>
        <span class="brand__name">Arbor Talent Consulting</span>
      </div>

      <div class="divider" aria-hidden="true"></div>

      <div class="contact">
        <p class="contact__name">Darren Lim</p>
        <p class="contact__title">Business Development Director</p>
        <address class="contact__address">
          Arbor Talent Consulting Private Limited<br>
          27 Wexley Street, #05-03B<br>
          Harbourgate Trade Building<br>
          Singapore 059317
        </address>
        <p class="contact__line">
          <svg class="contact__icon" viewBox="0 0 12 12" aria-hidden="true">
            <rect x="3" y="0.5" width="6" height="11" rx="1.2" fill="none" stroke="var(--brand-blue)" stroke-width="1.2"/>
            <circle cx="6" cy="9.6" r="0.7" fill="var(--brand-blue)"/>
          </svg>
          (+65) 98354417
        </p>
        <p class="contact__line">
          <svg class="contact__icon" viewBox="0 0 12 12" aria-hidden="true">
            <rect x="0.5" y="2.5" width="11" height="7" fill="var(--brand-blue)"/>
            <path d="M0.8 2.8 L6 6.6 L11.2 2.8" fill="none" stroke="var(--card-bg)" stroke-width="1"/>
          </svg>
          dlim@arbortalent-advisory.com
        </p>
        <p class="contact__alt">Alternative: arbortalentadvisory@mailbox-example.com</p>
      </div>
    </section>

    <section class="card card--brand" aria-label="Business card, brand side">
      <div class="brand">
        <span class="brand__dot" aria-hidden="true"></span>
        <span class="brand__name">Arbor Talent Consulting</span>
      </div>
      <p class="website">www.arbortalent-advisory.com</p>
    </section>
  </main>
</body>
</html>
```